Buch-/eBook-Cover für Sachbuch gesucht
Zielgruppe
We're selfpublishing nonfiction books. Interested are adults - mostly man (age range: 25-50) - who want to learn more about leadership at their workplaces.
Aufgabenstellung
The design should be clean and simple, title easy to read, good color contrast (the cover has to stand out from an white background).

```html
<!DOCTYPE html>
<html lang="en">
<head>
<meta charset="utf-8">
<title>Leadership – Book Cover</title>
<link rel="stylesheet" href="https://fonts.googleapis.com/css2?family=Bebas+Neue&family=Questrial&family=Raleway:wght@800&display=swap">
<style>
  :root {
    --backdrop: #333333;
    --cover-top: #efefef;
    --cover-bottom: #edd0a5;
    --ink: #333333;
  }
  html, body {
    margin: 0;
    padding: 0;
    width: 1075px;
    height: 1200px;
    overflow: hidden;
    background: var(--backdrop);
  }
  .canvas {
    position: relative;
    width: 1075px;
    height: 1200px;
    background: var(--backdrop);
  }
  .book-cover {
    position: absolute;
    left: 217px;
    top: 147px;
    width: 640px;
    height: 905px;
    background: var(--cover-bottom);
    color: var(--ink);
  }
  .cover-header {
    position: absolute;
    left: 0;
    top: 0;
    width: 640px;
    height: 298px;
    background: var(--cover-top);
    border-bottom: 1px solid #c9c2b6;
  }
  .rule {
    position: absolute;
    height: 2px;
    background: var(--ink);
  }
  .rule--top { left: 146px; width: 348px; top: 122px; }
  .rule--bottom { left: 218px; width: 204px; top: 203px; }
  .series-title {
    position: absolute;
    left: 0;
    width: 640px;
    top: 138px;
    margin: 0;
    text-align: center;
    font-family: "Bebas Neue", "Oswald", sans-serif;
    font-weight: 400;
    font-size: 66px;
    line-height: 66px;
    letter-spacing: 0.42em;
    text-indent: 0.42em;
  }
  .book-title {
    position: absolute;
    left: 0;
    width: 640px;
    top: 430px;
    margin: 0;
    text-align: center;
    font-family: "Questrial", "Didact Gothic", sans-serif;
    font-weight: 400;
    text-transform: uppercase;
    letter-spacing: 0.08em;
  }
  .book-title span { display: block; }
  .title-line { font-size: 44px; line-height: 54px; }
  .title-joiner { font-size: 31px; line-height: 44px; }
  .author {
    position: absolute;
    left: 0;
    width: 640px;
    top: 970px;
    top: 836px;
    margin: 0;
    text-align: center;
    font-family: "Raleway", "Arial", sans-serif;
    font-weight: 800;
    font-size: 26px;
    line-height: 30px;
  }
</style>
</head>
<body>
  <main class="canvas">
    <article class="book-cover">
      <header class="cover-header">
        <div class="rule rule--top"></div>
        <p class="series-title">Leadership</p>
        <div class="rule rule--bottom"></div>
      </header>
      <h1 class="book-title">
        <span class="title-line">Fostering</span>
        <span class="title-line">Growth</span>
        <span class="title-joiner">and</span>
        <span class="title-line">Inspiring</span>
        <span class="title-line">Excellence</span>
      </h1>
      <p class="author">Daniel Hartley</p>
    </article>
  </main>
</body>
</html>
```